Polystyrene Recycling Material Flow

We need a diagram styled as an infographic that shows how polystyrene foam is recycled starting with a manufactured product, moving through the distribution process, waste material collection and reincorporation back into manufacturing. This is accomplished in different ways once the material is collected which needs to be clearly evident. The most important thing is for it to be simple enough to understand while still having a stylish look. The design can be with or without vector images or photography to depict the different stages. We are providing a very rudimentary 'sketch' of the information points and movement flow. Please see www.foamtradecouncil.org (resources) to view our literature branding. The RGB & CMYK are attached.

Target Market(s)

Government Agencies, Brand Owners, Retailers, Recycling Industry

Industry/Entity Type

Packaging, Recycling, Manufacturing

Font styles to use
Sans Serif

Requirements
Must have
• Easy to Understand
Nice to have
• Images - either photography or vector illustrations - are optional. We have provided examples of both to show what could be used but are not required. Substituting your own interpretation of imagery is encouraged.
Should not have
• Outdated look.

```html
<!DOCTYPE html>
<html lang="en">
<head>
<meta charset="utf-8">
<title>Polystyrene Recycling Material Flow</title>
<link rel="stylesheet" href="https://fonts.googleapis.com/css2?family=Roboto:wght@500;700;900&display=swap">
<style>
:root{
  --bg-top:#eef6f8;
  --bg-bottom:#b9dde6;
  --panel:#ffffff;
  --ink:#111111;
  --green:#8cbc3f;
  --green-dark:#5f9a2a;
  --green-light:#c3dd84;
  --teal-dark:#2f8a79;
  --teal-light:#8fd0c2;
  --purple:#8e3f8f;
  --purple-dark:#5b1d5e;
  --violet:#a66bcf;
  --blue:#1a74c7;
  --blue-dark:#0f3f8d;
  --orange:#f39c1f;
  --orange-dark:#e0640d;
  --olive:#c9b213;
  --brown:#7a4e07;
  --pink:#e86f8a;
  --red:#d83a4d;
  --periwinkle:#7ea3d8;
  --sky:#e1f4fa;
  --dash:#8a8f94;
}
*{box-sizing:border-box;margin:0;padding:0}
html,body{width:1200px;height:845px;overflow:hidden}
body{font-family:"Roboto",Arial,sans-serif;color:var(--ink);background:linear-gradient(180deg,var(--bg-top),var(--bg-bottom))}
.canvas{position:relative;width:1200px;height:845px}
.abs{position:absolute}
.panel{position:absolute;background:var(--panel);border-radius:8px;box-shadow:0 4px 14px rgba(40,80,100,.12);overflow:hidden}
.panel-sources{left:108px;top:128px;width:601px;height:259px}
.panel-processing{left:108px;top:400px;width:719px;height:363px}
.panel-regrind{left:841px;top:478px;width:299px;height:285px}
.flow-lines{position:absolute;left:0;top:0;width:1200px;height:845px;pointer-events:none}
.hub{position:absolute;border-radius:50%;background:#fff;display:flex;align-items:center;justify-content:center;text-align:center;font-weight:500;font-size:10px;line-height:1.45}
.hub-sources{left:145px;top:203px;width:84px;height:84px;border:4px solid #7fd3e4}
.hub-compaction{left:246px;top:445px;width:84px;height:84px;border:4px solid #a4539c;font-size:10px}
.node{position:absolute;display:flex;align-items:center;gap:7px;font-weight:500;font-size:9.5px;white-space:nowrap}
.dot{border-radius:50%;display:flex;align-items:center;justify-content:center;flex:none;box-shadow:0 1px 3px rgba(0,0,0,.2)}
.dot svg{width:55%;height:55%}
.dot-lg{width:40px;height:40px}
.dot-sm{width:32px;height:32px}
.dot-xs{width:28px;height:28px}
.c-olive{background:radial-gradient(circle at 35% 30%,#e3d13a,var(--olive) 60%,#9c8700)}
.c-blue{background:radial-gradient(circle at 35% 30%,#3fa0e8,var(--blue) 60%,var(--blue-dark))}
.c-red{background:radial-gradient(circle at 35% 30%,#f07a86,var(--red) 70%)}
.c-brown{background:radial-gradient(circle at 35% 30%,#b58518,var(--brown) 70%);border:2px solid #d9b23a}
.c-pink{background:radial-gradient(circle at 35% 30%,#f7a7b6,var(--pink) 70%);border:2px solid #f6c4cf}
.c-peri{background:radial-gradient(circle at 35% 30%,#a9c4ec,var(--periwinkle) 70%);border:2px solid #d4e2f5}
.c-violet{background:radial-gradient(circle at 35% 30%,#c89ae6,var(--violet) 70%);border:2px solid #e3ccf2}
.collection{position:absolute;left:886px;top:161px;width:206px;height:206px;border-radius:50%;background:var(--green);border:5px solid #fff;box-shadow:0 0 0 8px var(--green);display:flex;align-items:center;justify-content:center;color:#fff;font-weight:700;font-size:26px;letter-spacing:.3px}
.art{position:absolute;border-radius:10px}
.art-recycler{left:121px;top:290px;width:143px;height:95px;background:linear-gradient(135deg,#f7b733,#6a3d8e);opacity:.55}
.art-collector{left:992px;top:385px;width:186px;height:93px;background:linear-gradient(135deg,#5f86c4,#1f9a4a);opacity:.5}
.art-roller{left:699px;top:427px;width:122px;height:88px;background:linear-gradient(135deg,#f7a81b,#5a6675);opacity:.55}
.art-loader{left:108px;top:686px;width:93px;height:58px;background:linear-gradient(135deg,#f7a81b,#5a6675);opacity:.55}
.art-truck{left:710px;top:686px;width:116px;height:71px;background:linear-gradient(135deg,#f7a81b,#3d4550);opacity:.55}
.pill{position:absolute;height:37px;border-radius:19px;display:flex;align-items:center;gap:10px;padding-left:5px;color:#fff;font-weight:700;font-size:8.4px;line-height:1.3;box-shadow:0 3px 6px rgba(0,0,0,.15)}
.pill .badge{width:28px;height:28px;border-radius:50%;background:#fff;display:flex;align-items:center;justify-content:center;flex:none}
.pill .badge svg{width:18px;height:18px}
.pill-green{background:linear-gradient(180deg,var(--green-light),var(--green-dark))}
.pill-purple{background:linear-gradient(180deg,var(--purple),var(--purple-dark))}
.pill-blue{background:linear-gradient(180deg,#2b8fd9,var(--blue-dark))}
.pill-teal{background:linear-gradient(180deg,var(--teal-light),var(--teal-dark));font-size:10px}
.pill-magenta{background:linear-gradient(180deg,#c77ac7,var(--purple));font-size:10px}
.pill-packaging{font-size:9.5px;height:45px;border-radius:23px}
.pill-packaging .badge{width:34px;height:34px}
.step{position:absolute;border-radius:50%;display:flex;flex-direction:column;align-items:center;justify-content:center;color:#fff;font-weight:700;text-align:center;box-shadow:0 3px 8px rgba(0,0,0,.2)}
.step svg{width:22px;height:22px;margin-bottom:4px}
.step-regrind{left:888px;top:486px;width:84px;height:84px;font-size:8.5px;line-height:1.05;background:radial-gradient(circle at 40% 25%,#f7b53a,var(--orange) 50%,var(--orange-dark));border:2px solid #fbc97a}
.step-shred{left:978px;top:491px;width:74px;height:74px;font-size:8px;background:radial-gradient(circle at 40% 25%,#3fa0e8,var(--blue) 50%,var(--blue-dark))}
.sub{position:absolute;text-align:center;font-weight:500;font-size:6.6px;line-height:1.5;width:70px}
.page-mark{position:absolute;left:1158px;top:813px;font-weight:700;font-size:12px}
</style>
</head>
<body>
<div class="canvas">

  <div class="panel panel-sources"></div>
  <div class="panel panel-processing">
    <svg class="abs" style="left:0;top:0" width="719" height="363" viewBox="0 0 719 363" aria-hidden="true">
      <path d="M0 0H607C590 90 450 160 250 157C150 155 60 140 0 122Z" fill="var(--sky)"/>
    </svg>
  </div>
  <div class="panel panel-regrind"></div>

  <svg class="flow-lines" viewBox="0 0 1200 845" aria-hidden="true">
    <defs>
      <marker id="arrow-grey" markerWidth="8" markerHeight="8" refX="4" refY="6" orient="auto" markerUnits="userSpaceOnUse">
        <path d="M0 2L4 6L8 2" fill="none" stroke="var(--dash)" stroke-width="1.4"/>
      </marker>
    </defs>
    <!-- outer dashed loops -->
    <path d="M108 571H34V71H1004V116" fill="none" stroke="var(--dash)" stroke-width="1.3" stroke-dasharray="5 4"/>
    <path d="M1000 112L1004 116L1008 112" fill="none" stroke="var(--dash)" stroke-width="1.4"/>
    <path d="M1140 571H1178V105H1047V132" fill="none" stroke="var(--dash)" stroke-width="1.3" stroke-dasharray="5 4"/>
    <path d="M1043 128L1047 132L1051 128" fill="none" stroke="var(--dash)" stroke-width="1.4"/>

    <!-- collection ring arcs -->
    <path d="M853 245A136 136 0 0 1 1112 232" fill="none" stroke="var(--green)" stroke-width="2"/>
    <path d="M1104 232L1122 258L1127 228Z" fill="var(--green)"/>

    <!-- source branches -->
    <g fill="none" stroke-width="2">
      <path d="M229 256C270 256 270 203 307 203" stroke="#a6dbe9" stroke-dasharray="2 1"/>
      <path d="M229 258H307" stroke="#a6dbe9" stroke-dasharray="2 1"/>
      <path d="M229 260C270 260 270 312 307 312" stroke="#a6dbe9" stroke-dasharray="2 1"/>
      <path d="M451 203H490C500 203 500 172 515 172" stroke="var(--green-light)"/>
      <path d="M490 203C500 203 500 234 515 234" stroke="var(--green-light)"/>
      <path d="M461 312H493C505 312 510 281 526 281" stroke="#f3a9b8"/>
      <path d="M493 312C505 312 510 344 526 344" stroke="#f3a9b8"/>
      <path d="M338 476H370C385 476 385 445 402 445" stroke="var(--periwinkle)"/>
      <path d="M370 476C385 476 385 508 402 508" stroke="var(--periwinkle)"/>
      <path d="M1015 566V580C1015 590 990 595 986 607" stroke="#c7a6e2"/>
      <path d="M1015 580C1015 590 1040 595 1045 607" stroke="#c7a6e2"/>
    </g>

    <!-- green dotted flow arrows -->
    <g fill="none" stroke="var(--green)" stroke-width="4" stroke-linecap="round" stroke-dasharray="0.1 11">
      <path d="M714 272H838"/>
      <path d="M890 340L840 400"/>
      <path d="M990 390V462"/>
    </g>
    <g fill="none" stroke="var(--green)" stroke-width="2.4">
      <path d="M836 264L845 272L836 280"/>
      <path d="M833 396V406H843"/>
      <path d="M982 462L990 472L998 462"/>
    </g>

    <!-- purple dotted flow arrows -->
    <g fill="none" stroke="#a65aa6" stroke-width="1.6" stroke-dasharray="2 3">
      <path d="M290 531V578"/>
      <path d="M290 625V636"/>
      <path d="M290 679V690"/>
      <path d="M629 624V652"/>
      <path d="M520 594L465 556"/>
    </g>
    <g fill="none" stroke="#a65aa6" stroke-width="1.4">
      <path d="M286 577L290 581L294 577"/>
      <path d="M286 635L290 639L294 635"/>
      <path d="M286 689L290 693L294 689"/>
      <path d="M625 652L629 656L633 652"/>
      <path d="M462 562V554H470"/>
    </g>
    <path d="M1014 650V673" stroke="var(--orange)" stroke-width="1.4" stroke-dasharray="2 2" fill="none"/>
    <path d="M1010 672L1014 676L1018 672" stroke="var(--orange)" stroke-width="1.4" fill="none"/>

    <!-- hub accent arcs -->
    <path d="M139 230A50 50 0 0 0 230 280" fill="none" stroke="#f08a3a" stroke-width="1.2"/>
    <path d="M240 470A50 50 0 0 0 330 520" fill="none" stroke="#e0507a" stroke-width="1.2"/>
  </svg>

  <!-- sources -->
  <div class="hub hub-sources">EPS WASTE<br>SOURCES</div>
  <div class="art art-recycler" role="img" aria-label="Illustration of a person dropping foam waste into a recycling bin"></div>

  <div class="node" style="left:307px;top:183px">
    <span class="dot dot-lg c-olive"><svg viewBox="0 0 24 24" fill="none" stroke="#fff" stroke-width="1.6"><path d="M5 7h14M7 7l1 13h8l1-13M10 4h4v3"/></svg></span>MUNICIPAL WASTE</div>
  <div class="node" style="left:307px;top:238px">
    <span class="dot dot-lg c-blue"><svg viewBox="0 0 24 24" fill="none" stroke="#fff" stroke-width="1.6"><path d="M3 20h18M5 20V9h3v11M10 20v-7l5-3v3l5-3v10"/></svg></span>MANUFACTURING WASTE</div>
  <div class="node" style="left:307px;top:292px">
    <span class="dot dot-lg c-red"><svg viewBox="0 0 24 24" fill="none" stroke="#fff" stroke-width="1.6"><path d="M4 20V8h6v12M10 20V4h7v16M3 20h18M6 11h2M6 14h2M12 7h3M12 10h3M12 13h3"/></svg></span>COMMERCIAL WASTE</div>

  <div class="node" style="left:515px;top:156px">
    <span class="dot dot-sm c-brown"><svg viewBox="0 0 24 24" fill="none" stroke="#fff" stroke-width="1.6"><path d="M4 20V10l8-5 8 5v10zM9 20v-5h6v5"/></svg></span>DROP-OFF CENTERS</div>
  <div class="node" style="left:515px;top:218px">
    <span class="dot dot-sm c-brown"><svg viewBox="0 0 24 24" fill="none" stroke="#fff" stroke-width="1.6"><path d="M3 20h18M5 20v-8h5v8M12 20v-6h7v6M8 8l2-3 2 3"/></svg></span>CURBSIDE COLLECTION</div>
  <div class="node" style="left:526px;top:265px">
    <span class="dot dot-sm c-pink"><svg viewBox="0 0 24 24" fill="none" stroke="#fff" stroke-width="1.6"><path d="M2 15V8h12v7M14 10h4l3 3v2H2"/><circle cx="6" cy="17" r="1.6"/><circle cx="17" cy="17" r="1.6"/></svg></span>BACK HAULING</div>
  <div class="node" style="left:526px;top:328px">
    <span class="dot dot-sm c-pink"><svg viewBox="0 0 24 24" fill="none" stroke="#fff" stroke-width="1.6"><path d="M12 21s-6-6-6-11a6 6 0 0 1 12 0c0 5-6 11-6 11z"/><circle cx="12" cy="10" r="2"/></svg></span>LOCALIZED DELIVERY</div>

  <!-- collection hub -->
  <div class="collection">COLLECTION</div>
  <div class="art art-collector" role="img" aria-label="Illustration of a person carrying paper waste beside green recycling containers"></div>

  <!-- compaction -->
  <div class="hub hub-compaction">COMPACTION</div>
  <div class="art art-roller" role="img" aria-label="Illustration of a yellow road roller"></div>
  <div class="node" style="left:402px;top:429px">
    <span class="dot dot-sm c-peri"><svg viewBox="0 0 24 24" fill="none" stroke="#fff" stroke-width="1.6"><circle cx="10" cy="12" r="4"/><path d="M16 5v14M19 5v14"/></svg></span>EXTRUDED INGOT</div>
  <div class="node" style="left:402px;top:492px">
    <span class="dot dot-sm c-peri"><svg viewBox="0 0 24 24" fill="none" stroke="#fff" stroke-width="1.6"><path d="M9 4h6v4H9zM8 8h8v12H8zM8 13h8"/></svg></span>HYDROLIC COMPRESSION</div>

  <div class="pill pill-green" style="left:225px;top:586px;width:200px">
    <span class="badge"><svg viewBox="0 0 24 24" fill="none" stroke="var(--green-dark)" stroke-width="1.6"><path d="M9 5l3-2 3 5M18 11l2 4-3 4h-5M7 19H4l-1-4 3-5"/></svg></span>RECYCLED CONTENT<br>EPS RESIN</div>
  <div class="pill pill-purple" style="left:225px;top:641px;width:200px">
    <span class="badge"><svg viewBox="0 0 24 24" fill="none" stroke="var(--purple)" stroke-width="1.6"><path d="M3 9h12a3 3 0 1 0-3-3M3 14h15a3 3 0 1 1-3 3"/></svg></span>RE-PALLETIZED WITH BLOWING<br>AGENT</div>
  <div class="pill pill-blue" style="left:225px;top:696px;width:200px">
    <span class="badge"><svg viewBox="0 0 24 24" fill="none" stroke="var(--blue)" stroke-width="1.6"><path d="M4 9l8-4 8 4v9l-8 4-8-4zM4 9l8 4 8-4M12 13v9"/></svg></span>EXPANDED POLYSTYRENE PACKAGING<br>&amp; BUILDING PRODUCTS ≤50%</div>

  <div class="pill pill-teal" style="left:520px;top:586px;width:200px">
    <span class="badge"><svg viewBox="0 0 24 24" fill="none" stroke="var(--teal-dark)" stroke-width="1.6"><path d="M3 8h8v10H3zM11 12h10v4H11"/></svg></span>EXTRUDED RIGID PS PALLET</div>
  <div class="pill pill-magenta" style="left:520px;top:660px;width:200px">
    <span class="badge"><svg viewBox="0 0 24 24" fill="none" stroke="var(--purple)" stroke-width="1.6"><circle cx="12" cy="7" r="4"/><path d="M4 21V15M8 21v-4M12 21v-6M16 21v-3M20 21v-7"/></svg></span>END MARKET APPLICATIONS</div>

  <div class="art art-loader" role="img" aria-label="Illustration of a yellow wheel loader"></div>
  <div class="art art-truck" role="img" aria-label="Illustration of a dump truck loaded with gravel"></div>

  <!-- regrind / shredding -->
  <div class="step step-regrind"><svg viewBox="0 0 24 24" fill="none" stroke="#fff" stroke-width="1.5"><path d="M5 20V9h5v11M10 20V5h8v15M3 20h18"/></svg>REGRIND<br>MOLDER<br>FACILITIES</div>
  <div class="step step-shred"><svg viewBox="0 0 24 24" fill="none" stroke="#fff" stroke-width="1.5"><path d="M6 3h12v7H6zM4 10h16v3H4zM7 13v7M10 13v7M13 13v7M16 13v7"/></svg>SHREDDING</div>

  <span class="dot dot-xs c-violet abs" style="left:972px;top:607px"><svg viewBox="0 0 24 24" fill="none" stroke="#fff" stroke-width="1.6"><path d="M6 20h12M9 20V8h6v12M9 4h8v4"/></svg></span>
  <span class="dot dot-xs c-violet abs" style="left:1031px;top:607px"><svg viewBox="0 0 24 24" fill="none" stroke="#fff" stroke-width="1.6"><circle cx="12" cy="12" r="7"/><circle cx="12" cy="12" r="3"/></svg></span>
  <div class="sub" style="left:951px;top:638px">HOMOGENIZATION</div>
  <div class="sub" style="left:1019px;top:638px">MIXING FOR<br>CONSISTENCY</div>

  <div class="pill pill-green pill-packaging" style="left:934px;top:678px;width:164px">
    <span class="badge"><svg viewBox="0 0 24 24" fill="none" stroke="var(--green-dark)" stroke-width="1.6"><path d="M9 5l3-2 3 5M18 11l2 4-3 4h-5M7 19H4l-1-4 3-5"/></svg></span>RECYCLED CONTENT<br>PACKAGING ≤15%</div>

  <div class="page-mark">C9</div>
</div>
</body>
</html>
```